Human Resource Consulting practice needs a business card design

We need a business card design (double sided colour) for our Human Resource (HR) consulting practice in regional New South Wales, australia. Our business name is Staff Compass. We support small and medium business across the Mid North Coast of New South Wales by providing them with outsourced HR support, services and products to help them achieve compliance with workplace legislation and across all areas of the employment lifecycle from recruitment to termination and everything in between. Our corporate colours are hot pink and black. The final design should communicate professionalism, trust, people focus.
I have attached the current (old) business card for your reference.

Target Market(s)

Business owners and high level managers

Industry/Entity Type

Business

Contact Information for Business Card

Name
Title
Phone no
Mobile no
Address
PO Box
email address
website

Colors
e34197

Requirements
Must have
• Tempate for changing business card personal details including Name, position title, mobile number, email address.
• Keep current logo and colours as per attached
• Logo must be presented in 2 colours or black only not white
Nice to have
• One side logo and graphic only other side logo and personal details
Should not have
• Should not be the same as the current version (attached) but a modern interpretation.
• Does not need a busy reverse side with our list of services as per current version. I feel this is too busy.
• No photos

```html
<!DOCTYPE html>
<html lang="en">
<head>
<meta charset="utf-8">
<title>Staff Compass – Business Card</title>
<link rel="stylesheet" href="https://fonts.googleapis.com/css2?family=Arimo:wght@400;700&family=Rajdhani:wght@500;600&display=swap">
<style>
  :root {
    --pink: #e34197;
    --black: #231f20;
    --card-dark: #2a2627;
    --white: #ffffff;
    --grey: #5a5a5a;
    --rule: #8a8a8a;
    --stage: #ece9e6;
  }
  * { box-sizing: border-box; margin: 0; padding: 0; }
  html, body { width: 1200px; height: 885px; overflow: hidden; }
  body {
    background: var(--stage);
    font-family: "Arimo", Arial, sans-serif;
    position: relative;
  }
  .card {
    position: absolute;
    top: 277px;
    width: 540px;
    height: 330px;
    border-radius: 18px;
    box-shadow: 0 10px 28px rgba(0,0,0,.18);
    overflow: hidden;
  }
  /* Front */
  .card-front { left: 40px; background: var(--white); color: var(--black); }
  .front-logo {
    position: absolute; left: 38px; top: 78px;
    display: flex; align-items: center; gap: 10px;
  }
  .logo-mark { width: 12px; height: 12px; background: var(--pink); flex: none; }
  .logo-name {
    font-family: "Arimo", Arial, sans-serif;
    font-weight: 700; font-size: 40px; color: var(--pink);
    letter-spacing: -0.5px; white-space: nowrap;
  }
  .person { position: absolute; right: 48px; top: 112px; text-align: right; }
  .person-name { font-weight: 700; font-size: 21px; line-height: 26px; color: var(--pink); }
  .person-title { font-size: 11px; letter-spacing: .6px; color: var(--black); margin-top: 3px; }
  .divider {
    position: absolute; left: 38px; right: 48px; top: 180px;
    height: 1px; background: var(--rule);
  }
  .contacts { position: absolute; left: 38px; top: 196px; list-style: none; }
  .contacts li {
    display: flex; align-items: center; gap: 10px;
    font-size: 15px; line-height: 26px; color: var(--black); white-space: nowrap;
  }
  .icon { width: 18px; height: 18px; flex: none; }
  .address {
    position: absolute; right: 48px; top: 202px; text-align: right;
    font-style: normal;
    font-family: "Rajdhani", Arial, sans-serif; font-weight: 600;
    font-size: 17px; line-height: 24px; color: var(--grey); white-space: nowrap;
  }
  /* Back */
  .card-back { left: 620px; background: var(--card-dark); color: var(--white); }
  .back-logo {
    position: absolute; left: 0; right: 0; top: 118px;
    display: flex; justify-content: center; align-items: center; gap: 12px;
  }
  .back-logo .logo-name { font-size: 46px; }
  .back-web {
    position: absolute; left: 0; right: 0; top: 208px;
    display: flex; justify-content: center; align-items: center; gap: 14px;
    font-family: "Rajdhani", Arial, sans-serif; font-weight: 500;
    font-size: 16px; letter-spacing: 1px; color: var(--white);
  }
  .back-web .line { width: 40px; height: 1px; background: #bdbdbd; }
</style>
</head>
<body>
  <section class="card card-front" aria-label="Card front">
    <div class="front-logo">
      <span class="logo-mark"></span>
      <span class="logo-name">Staff Compass</span>
    </div>
    <div class="person">
      <div class="person-name">Maree Holt</div>
      <div class="person-title">PRINCIPAL CONSULTANT</div>
    </div>
    <div class="divider"></div>
    <ul class="contacts">
      <li>
        <svg class="icon" viewBox="0 0 18 18" aria-hidden="true"><rect width="18" height="18" rx="3" fill="var(--pink)"/><path d="M5 4.5h2l1 2.5-1.3 1a6 6 0 0 0 2.8 2.8l1-1.3 2.5 1v2c0 .6-.5 1-1 1A8 8 0 0 1 4 5.5c0-.5.4-1 1-1z" fill="#fff"/></svg>
        02 6500 4182
      </li>
      <li>
        <svg class="icon" viewBox="0 0 18 18" aria-hidden="true"><rect width="18" height="18" rx="3" fill="var(--pink)"/><rect x="6" y="3.5" width="6" height="11" rx="1" fill="none" stroke="#fff" stroke-width="1.4"/><circle cx="9" cy="12.5" r=".8" fill="#fff"/></svg>
        0400 555 216
      </li>
      <li>
        <svg class="icon" viewBox="0 0 18 18" aria-hidden="true"><rect width="18" height="18" rx="3" fill="var(--pink)"/><rect x="3.5" y="5" width="11" height="8" fill="none" stroke="#fff" stroke-width="1.3"/><path d="M3.5 5 9 9.5 14.5 5" fill="none" stroke="#fff" stroke-width="1.3"/></svg>
        maree@staffcompass.com.au
      </li>
      <li>
        <svg class="icon" viewBox="0 0 18 18" aria-hidden="true"><rect width="18" height="18" rx="3" fill="var(--pink)"/><circle cx="9" cy="9" r="5" fill="none" stroke="#fff" stroke-width="1.3"/><ellipse cx="9" cy="9" rx="2.2" ry="5" fill="none" stroke="#fff" stroke-width="1.1"/><path d="M4 9h10" stroke="#fff" stroke-width="1.1"/></svg>
        www.staffcompass.com.au
      </li>
    </ul>
    <address class="address">
      P.O. Box 218<br>Kendall Bay, NSW 2499
    </address>
  </section>

  <section class="card card-back" aria-label="Card back">
    <div class="back-logo">
      <span class="logo-mark"></span>
      <span class="logo-name">Staff Compass</span>
    </div>
    <div class="back-web">
      <span class="line"></span>
      www.staffcompass.com.au
      <span class="line"></span>
    </div>
  </section>
</body>
</html>
```